Professional & attention grabbing.

A business card design, front and back. I already have a logo I will attach, but I am open to something new as well.
Things to include:
Name:
Title:
Phone:
Email:
Wanting something that is professional but attention grabbing.
Also we do a lot of work using drones on natural gas pipelines (leading the future)if you want to include any of that. I'm open to ideas.
Target Market(s)
Natural gas transmission industry / greenhouse gas mitigation industry
Industry/Entity Type
Business
Colors
Designer to choose colors to be used in the design.
Look and feel
Each slider illustrates characteristics of the customer's brand and the style your logo design should communicate.

```html
<!DOCTYPE html>
<html lang="en">
<head>
<meta charset="utf-8">
<title>Torvane Inspections – Business Card</title>
<link href="https://fonts.googleapis.com/css2?family=Montserrat:wght@500;600;700;800&display=swap" rel="stylesheet">
<style>
  :root {
    --brand-red: #c11f26;
    --ink-dark: #3a3a3c;
    --paper: #ffffff;
    --backdrop: #e4e4e4;
    --rule: #2d2d2d;
  }
  * { margin: 0; padding: 0; box-sizing: border-box; }
  html, body { width: 1200px; height: 1000px; overflow: hidden; }
  body {
    background: var(--backdrop);
    font-family: "Montserrat", Arial, sans-serif;
    position: relative;
  }
  .card {
    position: absolute;
    left: 220px;
    width: 760px;
    height: 434px;
    overflow: hidden;
    box-shadow: 0 6px 18px rgba(0,0,0,0.18);
  }
  .card-front { top: 50px; background: var(--brand-red); }
  .card-back { top: 516px; background: var(--paper); }

  .wordmark {
    display: flex;
    align-items: center;
    gap: 16px;
    font-weight: 800;
    text-transform: uppercase;
    letter-spacing: 0.5px;
  }
  .wordmark-square { display: block; flex: none; }

  .card-front .wordmark {
    position: absolute;
    left: 50%; top: 50%;
    transform: translate(-50%, -50%);
    color: var(--paper);
    font-size: 44px;
    white-space: nowrap;
  }
  .card-front .wordmark-square { width: 40px; height: 40px; background: var(--paper); }

  .card-back .wordmark {
    position: absolute;
    left: 40px; top: 38px;
    color: var(--ink-dark);
    font-size: 34px;
  }
  .card-back .wordmark-square { width: 32px; height: 32px; background: var(--brand-red); }

  .divider {
    position: absolute;
    left: 40px; top: 266px;
    width: 640px; height: 2px;
    background: var(--rule);
  }
  .contact {
    position: absolute;
    left: 40px; top: 284px;
    list-style: none;
    color: var(--ink-dark);
    font-weight: 500;
    font-size: 19px;
    line-height: 28px;
  }
  .contact li { display: flex; align-items: center; gap: 12px; }
  .contact svg { width: 15px; height: 15px; fill: var(--brand-red); flex: none; }

  .person {
    position: absolute;
    right: 60px; top: 280px;
    text-align: right;
    text-transform: uppercase;
  }
  .person-name { color: var(--brand-red); font-weight: 800; font-size: 26px; letter-spacing: 1px; }
  .person-title { color: var(--ink-dark); font-weight: 700; font-size: 18px; letter-spacing: 0.5px; margin-top: 2px; }

  .card-trim { position: absolute; left: 0; top: 0; width: 760px; height: 434px; }
</style>
</head>
<body>

  <section class="card card-front" aria-label="Card front">
    <div class="wordmark">
      <span class="wordmark-square"></span>
      <span>Torvane Inspections</span>
    </div>
  </section>

  <section class="card card-back" aria-label="Card back">
    <svg class="card-trim" viewBox="0 0 760 434" aria-hidden="true">
      <path d="M0 362 L470 378 L470 384 L0 372 Z" fill="var(--brand-red)"/>
      <path d="M0 388 L470 398 C490 398 500 384 525 384 L760 384 L760 434 L0 434 Z" fill="var(--brand-red)"/>
      <rect x="748" y="268" width="20" height="46" rx="8" fill="var(--brand-red)"/>
    </svg>

    <div class="wordmark">
      <span class="wordmark-square"></span>
      <span>Torvane Inspections</span>
    </div>

    <div class="divider"></div>

    <ul class="contact">
      <li>
        <svg viewBox="0 0 16 16"><path d="M2 6 C2 3 5 2 8 2 C11 2 14 3 14 6 L11 6 L10 4.5 L6 4.5 L5 6 Z M4 8 L12 8 L13 14 L3 14 Z"/></svg>
        <span>000 000 0000</span>
      </li>
      <li>
        <svg viewBox="0 0 16 16"><path d="M1 3 L15 3 L15 13 L1 13 Z M2 4.5 L8 9 L14 4.5" stroke="#fff" stroke-width="1"/></svg>
        <span>info@yourmail.com</span>
      </li>
    </ul>

    <div class="person">
      <div class="person-name">Daniel Reyes</div>
      <div class="person-title">Founder</div>
    </div>
  </section>

</body>
</html>
```